you will use Ai to Copy the website Brivanta.com to come up with the basic frame work and it will give you the understanding of how I would like Kelbrava.com to be like. Kelbrava.com is a peer to peer rv rental site very similar to both of the other rv rental sites the difference is that are commission based 20% and above per rental and we will be one flat monthly rate and they keep all the earnings. Below is photo that will help you with the color scheme and the look and feel of the design

1 page

```html
<!DOCTYPE html>
<html lang="en">
<head>
<meta charset="utf-8">
<title>Kelbrava.com – Home page concepts</title>
<link href="https://fonts.googleapis.com/css2?family=Inter:wght@400;500;600;700&family=Kalam:wght@400;700&display=swap" rel="stylesheet">
<style>
:root{
  --board:#858891;
  --navy:#12203f;
  --navy-deep:#0f1b36;
  --blue:#1f3a93;
  --green:#7dc243;
  --green-dark:#2f6b1f;
  --ink:#1d2433;
  --muted:#6b7280;
  --line:#e5e7eb;
  --white:#ffffff;
}
*{box-sizing:border-box;margin:0;padding:0}
html,body{width:1200px;height:1200px;overflow:hidden;background:var(--board);font-family:'Inter',sans-serif;color:var(--ink)}
.page{position:absolute;width:556px;height:1156px;background:var(--white);overflow:hidden;transform-origin:0 0;transform:scale(.6211)}
.page--browse{left:238.5px;top:188.8px}
.page--recent{left:615.5px;top:187px}
.abs{position:absolute}

/* hero */
.hero{position:absolute;left:0;top:0;width:556px;height:236px;background:linear-gradient(90deg,rgba(10,18,30,.55) 0%,rgba(10,18,30,.15) 60%,rgba(10,18,30,.05) 100%),linear-gradient(180deg,#3c4a5f 0%,#a8764a 28%,#d79a55 40%,#4a4f3e 60%,#1d261b 100%)}
.brand{font-family:'Inter',sans-serif;font-weight:700;color:var(--white);font-size:10px;letter-spacing:-.1px;line-height:1}
.brand--dark{color:var(--navy)}
.nav-link{font-size:6px;font-weight:500;color:var(--white);top:13px;line-height:1}
.nav-link--active{color:var(--green)}
.pill{border-radius:20px;font-weight:600;display:flex;align-items:center;justify-content:center;white-space:nowrap;line-height:1}
.pill--green{background:var(--green);color:var(--navy)}
.pill--blue{background:var(--blue);color:var(--white)}
.pill--outline{border:1px solid var(--green);color:var(--green)}
.icon-btn{width:11px;height:11px;border:1px solid var(--white);border-radius:50%}
.rate-mark{border-radius:50%;background:var(--green-dark)}
.hero-title{font-family:'Kalam',cursive;font-weight:400;color:var(--white);font-size:32px;line-height:38px;left:56px;top:80px;white-space:nowrap}
.hero-title .accent{color:var(--green)}
.hero-sub{left:56px;top:162px;font-size:7.2px;color:var(--white);line-height:1}
.search{left:56px;top:192px;width:445px;height:26px;background:var(--white);border-radius:14px}
.field{top:6px}
.field b{display:block;font-size:3.8px;line-height:5px;color:var(--muted);font-weight:600;letter-spacing:.3px}
.field span{display:block;font-size:5px;line-height:8px;color:var(--ink)}
.search-go{right:4px;top:3px;width:20px;height:20px;border-radius:50%;background:var(--blue)}

/* sidebar */
.side{left:38px;top:260px;width:140px;height:270px;border:1px solid var(--line);border-radius:4px;background:var(--white)}
.side-head{height:39px;border-bottom:1px solid var(--line);display:flex;align-items:center;justify-content:center}
.side-item{height:33px;border-bottom:1px solid var(--line);display:flex;align-items:center;padding-left:9px;font-size:6px;color:var(--ink)}
.side-item:last-child{border-bottom:0}
.side-item--active{color:var(--blue);font-weight:600}
.section-title{left:193px;top:260px;font-family:'Kalam',cursive;font-weight:400;font-size:18px;line-height:24px;color:var(--navy)}

.state{width:104px;height:54px;border:1px solid var(--line);border-radius:4px;padding:10px 9px}
.state svg{display:block;margin-bottom:7px}
.state b{display:block;font-size:5.3px;line-height:7px;font-weight:600}
.state span{display:block;font-size:5px;line-height:7px;color:var(--muted)}
.dots{display:flex;gap:2px}
.dots i{width:2px;height:2px;border-radius:50%;background:#c9ccd2;display:block}
.dots i:first-child{background:var(--green)}
.arrow{width:13px;height:13px;border-radius:50%;border:1px solid var(--line);display:flex;align-items:center;justify-content:center}
.arrow--fill{background:var(--blue);border-color:var(--blue)}

/* recent cards */
.photo{border-radius:4px}
.card-text{font-size:5.2px;color:var(--muted);line-height:1.6}

/* promos */
.promo{top:573px;height:115px;border-radius:4px;overflow:hidden}
.promo h3{font-size:8.6px;font-weight:700;color:var(--white);line-height:1.4}
.promo p{font-size:4.6px;color:#dfe4ea;line-height:1.5;margin-top:4px;width:130px}
.banner{left:39px;top:701px;width:478px;height:185px;border-radius:6px;background:linear-gradient(90deg,#132146 0%,#16244a 45%,#3a3e3e 70%,#24312a 100%)}
.banner .eyebrow{font-size:7px;color:var(--green);font-weight:600;line-height:1}
.banner h2{font-family:'Kalam',cursive;font-weight:400;font-size:25px;line-height:30px;color:var(--white);white-space:nowrap}

/* footer */
.footer{left:0;top:912px;width:556px;height:244px;background:var(--navy-deep);color:var(--white)}
.f-rule{background:rgba(255,255,255,.12)}
.f-title{font-size:7px;font-weight:600;line-height:1}
.f-text{font-size:4.8px;color:#b7c0d1;line-height:1.6}
.f-col h4{font-size:5.6px;font-weight:600;margin-bottom:8px;line-height:1}
.f-col a{display:block;font-size:4.6px;line-height:1;color:#aab4c6;text-decoration:none;margin-bottom:7.2px}
.store{width:37px;height:11px;border-radius:2px;background:#000;border:1px solid #555}
.social{width:7px;height:7px;border-radius:50%;background:var(--white)}
.input{border:1px solid rgba(255,255,255,.2);border-radius:10px;background:rgba(255,255,255,.05);font-size:4.8px;color:#8c96aa;display:flex;align-items:center;padding-left:7px}
</style>
</head>
<body>

<!-- ============ PAGE A : browse by state ============ -->
<section class="page page--browse">
  <header class="hero" role="img" aria-label="Photo of a green and white motorhome on a mountain lake road at sunset"></header>
  <div class="abs brand" style="left:20px;top:10px">Kelbrava.com</div>
  <div class="abs nav-link nav-link--active" style="left:219px">RV Rentals</div>
  <div class="abs nav-link" style="left:265px">Campgrounds</div>
  <div class="abs pill pill--green" style="left:442px;top:9px;width:57px;height:15px;font-size:5.6px">Become a host</div>
  <svg class="abs" style="left:510px;top:12px" width="8" height="7" viewBox="0 0 8 7"><path d="M0 .5h8M0 3.5h8M0 6.5h8" stroke="#fff"/></svg>
  <div class="abs icon-btn" style="left:525px;top:10px"></div>
  <div class="abs rate-mark" style="left:443px;top:34px;width:52px;height:52px" role="img" aria-label="Flat monthly rate badge"></div>
  <h1 class="abs hero-title">Adventure Awaits.<br>We Make It <span class="accent">Easy.</span></h1>
  <p class="abs hero-sub">Rent the perfect RV for your next journey. List it, rent it, bank it.</p>
  <div class="abs search">
    <div class="abs field" style="left:12px"><b>LOCATION</b><span>Houston, TX</span></div>
    <div class="abs field" style="left:121px"><b>DATES</b><span>Aug 14 - 16</span></div>
    <div class="abs field" style="left:193px"><b>GUESTS</b><span>2 guests</span></div>
    <div class="abs field" style="left:262px"><b>DRIVER'S AGE</b><span>25+</span></div>
    <div class="abs field" style="left:336px"><b>RENTAL TYPE</b><span>All types</span></div>
    <div class="abs search-go"><svg width="20" height="20" viewBox="0 0 20 20"><circle cx="9.5" cy="9.5" r="2.6" fill="none" stroke="#fff" stroke-width="1"/><path d="M11.4 11.4l2 2" stroke="#fff"/></svg></div>
  </div>

  <nav class="abs side">
    <div class="side-head"><span class="brand brand--dark" style="font-size:12px">Kelbrava.com</span></div>
    <div class="side-item">Best RV Rentals in the country</div>
    <div class="side-item">Rental near National Parks</div>
    <div class="side-item">Rental near State Parks</div>
    <div class="side-item">Signature Stay</div>
    <div class="side-item">Popular RV Rentals destination</div>
    <div class="side-item side-item--active">Browse RV Rentals by State</div>
    <div class="side-item">Recently Viewed</div>
  </nav>

  <h2 class="abs section-title">Browse RVs Rental by State</h2>
  <div class="abs state" style="left:193px;top:302px"><svg width="8" height="9"><rect x="1" y="1" width="6" height="7" rx="1" fill="none" stroke="#7dc243"/></svg><b>Alabama</b><span>516 RV Rentals</span></div>
  <div class="abs state" style="left:304px;top:302px"><svg width="8" height="9"><rect x="1" y="1" width="6" height="7" rx="1" fill="none" stroke="#7dc243"/></svg><b>Alaska</b><span>859 RV Rentals</span></div>
  <div class="abs state" style="left:415px;top:302px"><svg width="8" height="9"><rect x="1" y="1" width="6" height="7" rx="1" fill="none" stroke="#7dc243"/></svg><b>Arizona</b><span>1,144 RV Rentals</span></div>
  <div class="abs state" style="left:193px;top:363px"><svg width="10" height="9"><rect x="1" y="2" width="8" height="5" rx="1" fill="none" stroke="#7dc243"/></svg><b>Arkansas</b><span>1,144 RV Rentals</span></div>
  <div class="abs state" style="left:304px;top:363px"><svg width="8" height="9"><rect x="1" y="1" width="6" height="7" rx="1" fill="none" stroke="#7dc243"/></svg><b>California</b><span>6,292 RV Rentals</span></div>
  <div class="abs state" style="left:415px;top:363px"><svg width="10" height="9"><rect x="1" y="2" width="8" height="6" rx="1" fill="none" stroke="#7dc243"/></svg><b>Colorado</b><span>1,486 RV Rentals</span></div>
  <div class="abs state" style="left:193px;top:424px"><svg width="10" height="9"><rect x="1" y="2" width="8" height="5" rx="1" fill="none" stroke="#7dc243"/></svg><b>Connecticut</b><span>451 RV Rentals</span></div>
  <div class="abs state" style="left:304px;top:424px"><svg width="8" height="9"><rect x="1" y="1" width="6" height="7" rx="1" fill="none" stroke="#7dc243"/></svg><b>Delaware</b><span>463 RV Rentals</span></div>
  <div class="abs state" style="left:415px;top:424px"><svg width="8" height="9"><rect x="1" y="1" width="6" height="7" rx="1" fill="none" stroke="#7dc243"/></svg><b>Florida</b><span>2,453 RV Rentals</span></div>
  <div class="abs pill pill--blue" style="left:193px;top:494px;width:57px;height:16px;font-size:5px">View all states</div>
  <div class="abs dots" style="left:455px;top:501px"><i></i><i></i><i></i><i></i><i></i></div>
  <div class="abs arrow" style="left:486px;top:495px"><svg width="6" height="6"><path d="M5 3H1M3 1L1 3l2 2" stroke="#999" fill="none" stroke-width=".8"/></svg></div>
  <div class="abs arrow arrow--fill" style="left:505px;top:495px"><svg width="6" height="6"><path d="M1 3h4M3 1l2 2-2 2" stroke="#fff" fill="none" stroke-width=".8"/></svg></div>

  <div class="abs promo" style="left:39px;width:232px;background:linear-gradient(90deg,#1e2a24 0%,#4b5a46 55%,#8a8f78 100%)" role="img" aria-label="Photo of a motorhome parked at a mountain campsite with a campfire">
    <div class="abs" style="left:14px;top:34px"><h3>Less set up.<br>More Quality time.</h3><p>Love camping but don't love driving. Get an RV delivered and set up at location of your choice.</p></div>
    <div class="abs pill pill--green" style="left:14px;top:87px;width:60px;height:14px;font-size:5px">Get Delivered</div>
  </div>
  <div class="abs promo" style="left:285px;width:232px;background:linear-gradient(90deg,#1f2a38 0%,#4f5a60 55%,#9a8a70 100%)" role="img" aria-label="Photo of a motorhome driving on a mountain highway">
    <div class="abs" style="left:14px;top:53px"><h3>Pick it up &amp;<br>hit the road</h3></div>
    <div class="abs pill pill--blue" style="left:14px;top:87px;width:36px;height:14px;font-size:5px">Pick it up</div>
  </div>

  <div class="abs banner" role="img" aria-label="Photo of a motorhome at a lakeside campsite at dusk">
    <div class="abs eyebrow" style="left:38px;top:41px">Own an RV?</div>
    <h2 class="abs" style="left:38px;top:52px">List It. Rent It. Bank It.</h2>
    <div class="abs" style="left:38px;top:88px;font-size:7px;line-height:1;color:#fff">Join Kelbrava.com for one flat monthly rate</div>
    <div class="abs" style="left:38px;top:104px;font-size:8.6px;line-height:1;color:var(--green);font-weight:600">Keep 100% of your rental earnings!</div>
    <div class="abs pill pill--green" style="left:38px;top:129px;width:64px;height:16px;font-size:5.4px">Become a host</div>
    <div class="abs rate-mark" style="left:280px;top:92px;width:70px;height:70px"></div>
  </div>

  <footer class="abs footer">
    <div class="abs" style="left:38px;top:20px;width:23px;height:48px;border-radius:3px;background:linear-gradient(180deg,#6a5a40,#e8eaee 40%,#fff)" role="img" aria-label="Phone showing the Kelbrava app"></div>
    <div class="abs f-title" style="left:72px;top:23px">Kelbrava App</div>
    <div class="abs f-text" style="left:72px;top:35px">Manage trips, message hosts,<br>and hit the road—all in one app.</div>
    <div class="abs store" style="left:72px;top:56px"></div>
    <div class="abs store" style="left:113px;top:56px"></div>
    <div class="abs f-rule" style="left:196px;top:8px;width:1px;height:72px"></div>
    <svg class="abs" style="left:216px;top:30px" width="26" height="24" viewBox="0 0 26 24"><rect x="3" y="3" width="20" height="14" rx="6" fill="none" stroke="#7dc243" stroke-width="1.2"/><path d="M9 17l-2 5 6-5" fill="none" stroke="#7dc243" stroke-width="1.2"/><circle cx="9" cy="10" r="1" fill="#7dc243"/><circle cx="13" cy="10" r="1" fill="#7dc243"/><circle cx="17" cy="10" r="1" fill="#7dc243"/></svg>
    <div class="abs f-title" style="left:251px;top:20px">We're Here to Help</div>
    <div class="abs f-text" style="left:251px;top:32px">24/7 support for travelers and hosts.<br>Real people. Real answers.</div>
    <div class="abs pill pill--outline" style="left:251px;top:55px;width:64px;height:14px;font-size:5px">Contact Support</div>
    <div class="abs f-rule" style="left:357px;top:8px;width:1px;height:72px"></div>
    <div class="abs f-title" style="left:377px;top:21px"><span style="color:var(--green)">●</span> Follow Our Journey</div>
    <div class="abs social" style="left:377px;top:37px"></div>
    <div class="abs social" style="left:391px;top:37px"></div>
    <div class="abs social" style="left:405px;top:37px"></div>
    <div class="abs social" style="left:419px;top:37px"></div>
    <div class="abs f-text" style="left:377px;top:52px">Travel tips, destination ideas, and<br>inspiration for your next adventure.</div>
    <div class="abs f-rule" style="left:0;top:88px;width:556px;height:1px"></div>

    <div class="abs brand" style="left:40px;top:115px;font-size:9.5px">Kelbrava.com</div>
    <div class="abs f-text" style="left:38px;top:142px">The trusted marketplace for RV rentals<br>and RV owners. List it, rent it, bank it.</div>
    <div class="abs f-text" style="left:38px;top:172px;color:var(--green)">✓ Secure Booking</div>
    <div class="abs f-text" style="left:38px;top:186px;color:var(--green)">✓ Verified Hosts</div>
    <div class="abs f-text" style="left:38px;top:209px;font-size:4px;color:#6f7b93">© 2026 Kelbrava.com, LLC. All rights reserved.</div>
    <div class="abs f-col" style="left:177px;top:116px"><h4>For Travelers</h4><a>Find an RV</a><a>Delivery RVs</a><a>Road Trip RVs</a><a>Destinations</a><a>How it Works</a><a>Travel Guides</a><a>Insurance Options</a></div>
    <div class="abs f-col" style="left:245px;top:116px"><h4>For Hosts</h4><a>List Your RV</a><a>Why Kelbrava</a><a>Host Resources</a><a>Pricing</a><a>Host Support</a><a>Success Stories</a></div>
    <div class="abs f-col" style="left:313px;top:116px"><h4>Company</h4><a>About Us</a><a>Careers</a><a>Press</a><a>Partner With Us</a><a>Blog</a><a>Contact Us</a></div>
    <div class="abs f-col" style="left:381px;top:116px"><h4>Support</h4><a>Help Center</a><a>Safety</a><a>Cancellation Policy</a><a>Terms of Service</a><a>Privacy Policy</a></div>
    <div class="abs f-col" style="left:449px;top:116px;width:68px"><h4>Stay in the Loop</h4><div class="f-text" style="font-size:4.4px">Get travel inspiration and special offers delivered to your inbox.</div></div>
    <div class="abs input" style="left:449px;top:163px;width:68px;height:16px">Enter your email</div>
    <div class="abs pill pill--green" style="left:449px;top:185px;width:68px;height:16px;font-size:5.4px">Subscribe</div>
  </footer>
</section>

<!-- ============ PAGE B : recently viewed ============ -->
<section class="page page--recent">
  <header class="hero" role="img" aria-label="Photo of a green and white motorhome on a mountain lake road at sunset"></header>
  <div class="abs brand" style="left:20px;top:10px">Kelbrava.com</div>
  <div class="abs nav-link nav-link--active" style="left:219px">RV Rentals</div>
  <div class="abs nav-link" style="left:265px">Campgrounds</div>
  <div class="abs pill pill--green" style="left:442px;top:9px;width:57px;height:15px;font-size:5.6px">Become a host</div>
  <svg class="abs" style="left:510px;top:12px" width="8" height="7" viewBox="0 0 8 7"><path d="M0 .5h8M0 3.5h8M0 6.5h8" stroke="#fff"/></svg>
  <div class="abs icon-btn" style="left:525px;top:10px"></div>
  <div class="abs rate-mark" style="left:443px;top:34px;width:52px;height:52px" role="img" aria-label="Flat monthly rate badge"></div>
  <h1 class="abs hero-title">Adventure Awaits.<br>We Make It <span class="accent">Easy.</span></h1>
  <p class="abs hero-sub">Rent the perfect RV for your next journey. List it, rent it, bank it.</p>
  <div class="abs search">
    <div class="abs field" style="left:12px"><b>LOCATION</b><span>Houston, TX</span></div>
    <div class="abs field" style="left:121px"><b>DATES</b><span>Aug 14 - 16</span></div>
    <div class="abs field" style="left:193px"><b>GUESTS</b><span>2 guests</span></div>
    <div class="abs field" style="left:262px"><b>DRIVER'S AGE</b><span>25+</span></div>
    <div class="abs field" style="left:336px"><b>RENTAL TYPE</b><span>All types</span></div>
    <div class="abs search-go"><svg width="20" height="20" viewBox="0 0 20 20"><circle cx="9.5" cy="9.5" r="2.6" fill="none" stroke="#fff" stroke-width="1"/><path d="M11.4 11.4l2 2" stroke="#fff"/></svg></div>
  </div>

  <nav class="abs side">
    <div class="side-head"><span class="brand brand--dark" style="font-size:12px">Kelbrava.com</span></div>
    <div class="side-item">Best RV Rentals in the country</div>
    <div class="side-item">Rental near National Parks</div>
    <div class="side-item">Rental near State Parks</div>
    <div class="side-item">Signature Stay</div>
    <div class="side-item">Popular RV Rentals destination</div>
    <div class="side-item">Browse RV Rentals by State</div>
    <div class="side-item side-item--active">Recently Viewed</div>
  </nav>

  <h2 class="abs section-title">Recently Viewed</h2>
  <div class="abs photo" style="left:193px;top:302px;width:157px;height:101px;background:linear-gradient(160deg,#6d6a44 0%,#3e4a33 55%,#2c3350 100%)" role="img" aria-label="Photo of a glamping campsite in the Texas Hill Country">
    <div class="abs" style="left:12px;top:12px;font-size:12px;line-height:1;color:#fff;font-weight:500">Hill Country, TX</div>
    <div class="abs" style="left:12px;top:29px;font-size:5px;line-height:1;color:#e5e7eb">Montana</div>
    <div class="abs pill pill--green" style="left:12px;top:46px;width:46px;height:13px;font-size:5px">Book now</div>
    <div class="abs" style="left:12px;top:72px;width:73px;height:14px;border-radius:2px;background:rgba(255,255,255,.35)"></div>
  </div>
  <p class="abs card-text" style="left:193px;top:411px;width:158px">Enjoy a chill summer in the Texas Hill Country: a spring lake, sunrise hikes, starry nights, and luxurious air-conditioned glamping tents.</p>
  <div class="abs photo" style="left:362px;top:302px;width:157px;height:101px;background:linear-gradient(180deg,#dfe6ee 0%,#c7ced8 60%,#9aa3ad 100%)" role="img" aria-label="Photo of a white fifth-wheel travel trailer">
    <div class="abs pill" style="left:6px;top:6px;width:28px;height:9px;font-size:3.8px;background:#fff;color:var(--ink)">Highly rated</div>
    <div class="abs pill" style="left:127px;top:6px;width:24px;height:9px;font-size:4px;background:#fff;color:var(--ink)">28 ♡</div>
    <div class="abs dots" style="left:68px;top:92px"><i style="background:#fff"></i><i></i><i></i><i></i><i></i></div>
  </div>
  <div class="abs" style="left:364px;top:411px;font-size:6px;line-height:1;font-weight:500">2024 Wind Jamming Ridgeway Sport</div>
  <div class="abs card-text" style="left:364px;top:420px">Fifth-wheel • Sleeps 7 • 31 ft<br>Lynn Haven, FL</div>
  <div class="abs" style="left:364px;top:443px;font-size:6px;line-height:1;font-weight:700">$110 <span style="font-weight:400;color:var(--muted);font-size:4.6px">/night</span></div>
  <div class="abs" style="left:493px;top:444px;font-size:4.6px;line-height:1;color:var(--ink)"><span style="color:var(--green)">★</span> 5.0 <span style="color:var(--muted)">(8)</span></div>

  <div class="abs promo" style="left:39px;width:232px;background:linear-gradient(90deg,#1e2a24 0%,#4b5a46 55%,#8a8f78 100%)" role="img" aria-label="Photo of a motorhome parked at a mountain campsite with a campfire">
    <div class="abs" style="left:14px;top:34px"><h3>Less set up.<br>More Quality time.</h3><p>Love camping but don't love driving. Get an RV delivered and set up at location of your choice.</p></div>
    <div class="abs pill pill--green" style="left:14px;top:87px;width:60px;height:14px;font-size:5px">Get Delivered</div>
  </div>
  <div class="abs promo" style="left:285px;width:232px;background:linear-gradient(90deg,#1f2a38 0%,#4f5a60 55%,#9a8a70 100%)" role="img" aria-label="Photo of a motorhome driving on a mountain highway">
    <div class="abs" style="left:14px;top:53px"><h3>Pick it up &amp;<br>hit the road</h3></div>
    <div class="abs pill pill--blue" style="left:14px;top:87px;width:36px;height:14px;font-size:5px">Pick it up</div>
  </div>

  <div class="abs banner" role="img" aria-label="Photo of a motorhome at a lakeside campsite at dusk">
    <div class="abs eyebrow" style="left:38px;top:41px">Own an RV?</div>
    <h2 class="abs" style="left:38px;top:52px">List It. Rent It. Bank It.</h2>
    <div class="abs" style="left:38px;top:88px;font-size:7px;line-height:1;color:#fff">Join Kelbrava.com for one flat monthly rate</div>
    <div class="abs" style="left:38px;top:104px;font-size:8.6px;line-height:1;color:var(--green);font-weight:600">Keep 100% of your rental earnings!</div>
    <div class="abs pill pill--green" style="left:38px;top:129px;width:64px;height:16px;font-size:5.4px">Become a host</div>
    <div class="abs rate-mark" style="left:280px;top:92px;width:70px;height:70px"></div>
  </div>

  <footer class="abs footer">
    <div class="abs" style="left:38px;top:20px;width:23px;height:48px;border-radius:3px;background:linear-gradient(180deg,#6a5a40,#e8eaee 40%,#fff)" role="img" aria-label="Phone showing the Kelbrava app"></div>
    <div class="abs f-title" style="left:72px;top:23px">Kelbrava App</div>
    <div class="abs f-text" style="left:72px;top:35px">Manage trips, message hosts,<br>and hit the road—all in one app.</div>
    <div class="abs store" style="left:72px;top:56px"></div>
    <div class="abs store" style="left:113px;top:56px"></div>
    <div class="abs f-rule" style="left:196px;top:8px;width:1px;height:72px"></div>
    <svg class="abs" style="left:216px;top:30px" width="26" height="24" viewBox="0 0 26 24"><rect x="3" y="3" width="20" height="14" rx="6" fill="none" stroke="#7dc243" stroke-width="1.2"/><path d="M9 17l-2 5 6-5" fill="none" stroke="#7dc243" stroke-width="1.2"/><circle cx="9" cy="10" r="1" fill="#7dc243"/><circle cx="13" cy="10" r="1" fill="#7dc243"/><circle cx="17" cy="10" r="1" fill="#7dc243"/></svg>
    <div class="abs f-title" style="left:251px;top:20px">We're Here to Help</div>
    <div class="abs f-text" style="left:251px;top:32px">24/7 support for travelers and hosts.<br>Real people. Real answers.</div>
    <div class="abs pill pill--outline" style="left:251px;top:55px;width:64px;height:14px;font-size:5px">Contact Support</div>
    <div class="abs f-rule" style="left:357px;top:8px;width:1px;height:72px"></div>
    <div class="abs f-title" style="left:377px;top:21px"><span style="color:var(--green)">●</span> Follow Our Journey</div>
    <div class="abs social" style="left:377px;top:37px"></div>
    <div class="abs social" style="left:391px;top:37px"></div>
    <div class="abs social" style="left:405px;top:37px"></div>
    <div class="abs social" style="left:419px;top:37px"></div>
    <div class="abs f-text" style="left:377px;top:52px">Travel tips, destination ideas, and<br>inspiration for your next adventure.</div>
    <div class="abs f-rule" style="left:0;top:88px;width:556px;height:1px"></div>

    <div class="abs brand" style="left:40px;top:115px;font-size:9.5px">Kelbrava.com</div>
    <div class="abs f-text" style="left:38px;top:142px">The trusted marketplace for RV rentals<br>and RV owners. List it, rent it, bank it.</div>
    <div class="abs f-text" style="left:38px;top:172px;color:var(--green)">✓ Secure Booking</div>
    <div class="abs f-text" style="left:38px;top:186px;color:var(--green)">✓ Verified Hosts</div>
    <div class="abs f-text" style="left:38px;top:209px;font-size:4px;color:#6f7b93">© 2026 Kelbrava.com, LLC. All rights reserved.</div>
    <div class="abs f-col" style="left:177px;top:116px"><h4>For Travelers</h4><a>Find an RV</a><a>Delivery RVs</a><a>Road Trip RVs</a><a>Destinations</a><a>How it Works</a><a>Travel Guides</a><a>Insurance Options</a></div>
    <div class="abs f-col" style="left:245px;top:116px"><h4>For Hosts</h4><a>List Your RV</a><a>Why Kelbrava</a><a>Host Resources</a><a>Pricing</a><a>Host Support</a><a>Success Stories</a></div>
    <div class="abs f-col" style="left:313px;top:116px"><h4>Company</h4><a>About Us</a><a>Careers</a><a>Press</a><a>Partner With Us</a><a>Blog</a><a>Contact Us</a></div>
    <div class="abs f-col" style="left:381px;top:116px"><h4>Support</h4><a>Help Center</a><a>Safety</a><a>Cancellation Policy</a><a>Terms of Service</a><a>Privacy Policy</a></div>
    <div class="abs f-col" style="left:449px;top:116px;width:68px"><h4>Stay in the Loop</h4><div class="f-text" style="font-size:4.4px">Get travel inspiration and special offers delivered to your inbox.</div></div>
    <div class="abs input" style="left:449px;top:163px;width:68px;height:16px">Enter your email</div>
    <div class="abs pill pill--green" style="left:449px;top:185px;width:68px;height:16px;font-size:5.4px">Subscribe</div>
  </footer>
</section>

</body>
</html>
```